Dog treat bakery needs updated bag labels

We're a small-batch dog treat bakery and would like to update our front bag labels to 1) differentiate our line of products and 2) to stand out on shelves. We believe all dogs deserve to eat clean, healthy foods. That's why we bake low-calorie, clean treats made with simple, premium ingredients like teff, amaranth, and sorghum flours and 100% blueberry, carrot, and purple sweet potato. All our treats are made gluten free without preservatives, artificial flavors, soy, corn, wheat, or eggs. Clean treats, happy dogs!

Logo Text

see uploaded files

```html
<!DOCTYPE html>
<html lang="en">
<head>
<meta charset="utf-8">
<title>Goofy Pup – Clean Treats Bag Label</title>
<link rel="stylesheet" href="https://fonts.googleapis.com/css2?family=Kurale&family=Open+Sans:wght@400;700&display=swap">
<style>
  :root {
    --backdrop-light: #fbe9d2;
    --backdrop-deep: #f4cf9c;
    --label-cream: #eeeacb;
    --label-cream-light: #f6f4e2;
    --badge-blue: #cfe8ee;
    --badge-blue-light: #e4f6f8;
    --accent-orange: #eb5b1e;
    --accent-orange-soft: #f07a2a;
    --accent-blue: #1ba3e4;
    --ink: #1d1d1b;
  }
  html, body {
    margin: 0;
    padding: 0;
    width: 1200px;
    height: 1163px;
    overflow: hidden;
  }
  body {
    position: relative;
    background: radial-gradient(ellipse at 50% 45%, var(--backdrop-light) 0%, var(--backdrop-deep) 100%);
    font-family: "Open Sans", sans-serif;
  }
  .label {
    position: absolute;
    left: 300px;
    top: 110px;
    width: 580px;
    height: 855px;
    overflow: hidden;
    background: radial-gradient(ellipse at 50% 30%, var(--label-cream-light) 0%, var(--label-cream) 70%);
  }
  .badge {
    position: absolute;
    left: -45px;
    top: 208px;
    width: 670px;
    height: 670px;
    border-radius: 50%;
    background: radial-gradient(circle at 50% 50%, var(--badge-blue-light) 0%, var(--badge-blue) 75%);
  }
  .tagline {
    position: absolute;
    left: 0;
    width: 100%;
    text-align: center;
    font-family: "Kurale", serif;
    margin: 0;
  }
  .tagline-main {
    top: 78px;
    font-size: 46px;
    color: var(--accent-orange);
    letter-spacing: 1px;
  }
  .tagline-sub {
    top: 138px;
    font-size: 33px;
    color: var(--accent-orange-soft);
    letter-spacing: 1px;
  }
  .brand-name {
    position: absolute;
    left: 0;
    top: 250px;
    width: 100%;
    text-align: center;
    margin: 0;
    font-family: "Open Sans", sans-serif;
    font-weight: 700;
    font-size: 62px;
    letter-spacing: 3px;
    color: var(--accent-orange);
  }
  .brand-mark {
    position: absolute;
    left: 172px;
    top: 340px;
    width: 236px;
    height: 236px;
    border-radius: 50%;
    background: var(--accent-blue);
  }
  .ingredients {
    position: absolute;
    left: 0;
    top: 668px;
    width: 100%;
    text-align: center;
  }
  .ingredients-title {
    margin: 0 0 2px;
    font-size: 21px;
    font-weight: 400;
    color: var(--accent-blue);
  }
  .ingredients-copy {
    margin: 0;
    font-size: 14.5px;
    line-height: 20px;
    color: var(--ink);
  }
</style>
</head>
<body>
  <main class="label">
    <div class="badge"></div>
    <p class="tagline tagline-main">happy dogs</p>
    <p class="tagline tagline-sub">Clean treats</p>
    <h1 class="brand-name">GOOFY PUP</h1>
    <div class="brand-mark"></div>
    <section class="ingredients">
      <h2 class="ingredients-title">premium ingredients</h2>
      <p class="ingredients-copy">
        like teff, amaranth, and sorghum flours<br>
        and %100 blueberry, carrot,<br>
        and purple sweet potato.<br>
        All our treats are made gluten free<br>
        without preservatives,<br>
        artificial flavors, soy, corn, wheat, or eggs.
      </p>
    </section>
  </main>
</body>
</html>
```